Calvanto Group Real Estate Company business cards

New business card design, we are generally happy with the basic layout of the existing front of business card, (feel free to change) but require a head shot photo on the back side.

http://www.calvanto.com.au/

Attached logos, and existing business card

------------------------------

Target Market(s)

Real estate

Industry/Entity Type

Real Estate

Contact Information for Business Card

Standard size double sided

Font styles to use
Other font styles liked:
• Futura

Requirements
Must have
• Photo head shot on the back side
Nice to have
• yes
Should not have
• No

```html
<!DOCTYPE html>
<html lang="en">
<head>
<meta charset="utf-8">
<title>Calvanto Group – Business Card</title>
<link rel="stylesheet" href="https://fonts.googleapis.com/css2?family=Fira+Sans:wght@400;500;600&display=swap">
<style>
  :root {
    --page-bg: #e9e7e4;
    --card-white: #fbfbfc;
    --navy: #2b2550;
    --navy-deep: #1f1a40;
    --orange: #e8701f;
    --text-light: #e4e2ee;
    --photo-top: #c9c6c2;
    --photo-bottom: #6f6d78;
  }
  html, body {
    margin: 0;
    width: 1200px;
    height: 969px;
    overflow: hidden;
    background: var(--page-bg);
    font-family: "Fira Sans", Arial, sans-serif;
  }
  .business-card {
    position: absolute;
    left: 100px;
    top: 200px;
    width: 1000px;
    height: 568px;
    background: var(--card-white);
    border-radius: 4px;
    box-shadow: 0 10px 30px rgba(0,0,0,0.18);
    overflow: hidden;
  }
  .card-art {
    position: absolute;
    inset: 0;
  }
  .brand-name {
    position: absolute;
    left: 70px;
    top: 118px;
    margin: 0;
    color: var(--navy);
    font-weight: 500;
    font-size: 76px;
    line-height: 1;
    letter-spacing: -1px;
  }
  .brand-name .brand-sub {
    display: block;
    text-align: right;
    font-size: 16px;
    letter-spacing: 6px;
    margin-top: 4px;
  }
  .services {
    position: absolute;
    left: 175px;
    top: 233px;
    margin: 0;
    color: var(--navy);
    font-weight: 600;
    font-size: 26px;
    word-spacing: 6px;
  }
  .contact-person {
    position: absolute;
    right: 518px;
    top: 402px;
    text-align: right;
    color: var(--text-light);
  }
  .contact-person .person-name {
    margin: 0;
    color: var(--orange);
    font-weight: 500;
    font-size: 34px;
    line-height: 44px;
  }
  .contact-person .person-role,
  .contact-person .person-email {
    margin: 0;
    font-size: 24px;
    line-height: 40px;
  }
  .contact-divider {
    position: absolute;
    left: 507px;
    top: 404px;
    width: 1px;
    height: 122px;
    background: rgba(255,255,255,0.45);
  }
  .company-details {
    position: absolute;
    left: 533px;
    top: 404px;
    margin: 0;
    padding: 0;
    list-style: none;
    color: var(--text-light);
    font-size: 24px;
  }
  .company-details li {
    display: flex;
    align-items: center;
    gap: 14px;
    height: 40px;
  }
  .company-details .detail-icon {
    width: 24px;
    height: 24px;
    flex: none;
  }
</style>
</head>
<body>
  <div class="business-card">
    <svg class="card-art" viewBox="0 0 1000 568" width="1000" height="568" aria-hidden="false">
      <defs>
        <linearGradient id="photoTone" x1="0" y1="0" x2="0" y2="1">
          <stop offset="0" stop-color="var(--photo-top)"/>
          <stop offset="1" stop-color="var(--photo-bottom)"/>
        </linearGradient>
        <linearGradient id="bandTone" x1="0" y1="0" x2="1" y2="0">
          <stop offset="0" stop-color="#352e63"/>
          <stop offset="1" stop-color="var(--navy-deep)"/>
        </linearGradient>
      </defs>
      <rect class="headshot-area" x="680" y="0" width="320" height="345" fill="url(#photoTone)" role="img" aria-label="Head-and-shoulders portrait of the director in a dark suit and blue tie"/>
      <path class="orange-swoosh" d="M0,288 C150,340 350,360 560,356 C750,352 880,342 1000,332 L1000,340 C900,348 800,362 700,372 C500,396 250,394 0,344 Z" fill="var(--orange)"/>
      <path class="navy-band" d="M0,348 C250,398 500,400 700,376 C820,362 920,348 1000,344 L1000,568 L0,568 Z" fill="url(#bandTone)"/>
      <path class="white-pinline" d="M620,378 C780,362 900,348 1000,342" stroke="#ffffff" stroke-width="2" fill="none" opacity="0.8"/>
    </svg>

    <h1 class="brand-name">calvanto<span class="brand-sub">GROUP</span></h1>
    <p class="services">Buy&nbsp;&nbsp;|&nbsp;&nbsp;Sell&nbsp;&nbsp;|&nbsp;&nbsp;Rent</p>

    <div class="contact-person">
      <p class="person-name">Daniel Tran</p>
      <p class="person-role">Director</p>
      <p class="person-email">daniel.tran@calvanto.com.au</p>
    </div>

    <div class="contact-divider"></div>

    <ul class="company-details">
      <li>ABN: 41 528 063 917</li>
      <li>
        <svg class="detail-icon" viewBox="0 0 24 24" aria-hidden="true">
          <path d="M6.6 3.5 9.4 3l1.6 4.2-2 1.4c1 2.3 2.8 4.1 5.1 5.1l1.4-2 4.2 1.6-.5 2.8c-.2.9-1 1.5-1.9 1.4C10.4 17 7 13.6 6.5 6.7 6.4 5.8 5.7 3.7 6.6 3.5Z" fill="var(--orange)"/>
        </svg>
        <span>0412 586 307</span>
      </li>
      <li>
        <svg class="detail-icon" viewBox="0 0 24 24" aria-hidden="true">
          <circle cx="12" cy="12" r="10" fill="var(--orange)"/>
          <path d="M5 9c3 0 4 2 3 4s1 4 2 6M14 3c-1 2 1 3 3 3s2 3 1 5-2 3 0 5" stroke="var(--navy-deep)" stroke-width="1.6" fill="none"/>
        </svg>
        <span>www.calvanto.com.au</span>
      </li>
    </ul>
  </div>
</body>
</html>
```